We are looking to create a graphic that will be used in Facebook posts each week to show the daily Mosquito Forecast. Attached is an example of what we are looking for. We need to be able to update the forecast. So we will need hi-res vector files. The graphics need to represent the level of mosquito activity: SLIGHT, AVERAGE, INTENSE, EXTREME

```html
<!DOCTYPE html>
<html lang="en">
<head>
<meta charset="utf-8">
<title>Mosquito Forecast</title>
<link rel="stylesheet" href="https://fonts.googleapis.com/css2?family=Open+Sans:wght@400;600;700&family=Oswald:wght@500&family=Poppins:wght@500&family=PT+Serif&family=Montserrat:wght@700&display=swap">
<style>
  :root {
    --slight: #0f9d4f;
    --slight-light: #2fc46f;
    --average: #fbb813;
    --average-light: #ffd84a;
    --intense: #e9692a;
    --intense-light: #f89248;
    --extreme: #d71f2b;
    --extreme-light: #f04a4f;
    --ink: #1f2a0f;
    --text: #2b2b2b;
    --board-top: #cdced0;
    --board-bottom: #e2e3e5;
    --rule: #c9c9c9;
  }
  * { box-sizing: border-box; margin: 0; padding: 0; }
  html, body { width: 1200px; height: 1014px; overflow: hidden; background: #fff; }
  body { position: relative; font-family: "Open Sans", sans-serif; }

  .board-head {
    position: absolute; left: 0; top: 0; width: 1200px; height: 792px;
    background: linear-gradient(180deg, var(--board-top), var(--board-bottom));
  }
  .board-title {
    position: absolute; left: 0; width: 1200px; top: 48px; text-align: center;
    font-weight: 700; font-size: 57px; line-height: 1; color: var(--ink); letter-spacing: -0.5px;
  }
  .board-subtitle {
    position: absolute; left: 0; width: 1200px; top: 134px; text-align: center;
    font-weight: 600; font-size: 24px; color: var(--ink);
  }

  .post { position: absolute; left: 118px; top: 254px; width: 965px; height: 490px; overflow: hidden; }
  .post-photo {
    position: absolute; inset: 0;
    background:
      linear-gradient(180deg, rgba(0,0,0,0) 70%, #2f5a1f 86%, #3f7a2a 100%),
      linear-gradient(180deg, #9aa6ad 0%, #5b6368 22%, #3b4140 45%, #4a5346 62%, #35522a 100%);
  }
  .post-title {
    position: absolute; left: 0; width: 100%; top: 48px; text-align: center;
    font-family: "Oswald", sans-serif; font-weight: 500; font-size: 104px; line-height: 1;
    color: #fff; letter-spacing: -1px; text-shadow: 0 2px 6px rgba(0,0,0,.35);
    transform: scaleX(.93);
  }
  .post-area {
    position: absolute; left: 0; width: 100%; top: 147px; text-align: center;
    font-family: "Poppins", sans-serif; font-weight: 500; font-size: 38px; line-height: 1.2;
    color: #fff; text-shadow: 0 2px 5px rgba(0,0,0,.4);
  }

  .forecast-panel { position: absolute; left: 16px; top: 211px; width: 930px; height: 262px; background: #fff; }
  .forecast-days { position: absolute; left: 9px; top: 0; width: 913px; height: 219px; display: grid; grid-template-columns: repeat(7, 1fr); }
  .day { position: relative; height: 219px; }
  .day + .day::before { content: ""; position: absolute; left: 0; top: 51px; bottom: 0; width: 1px; background: var(--rule); }
  .day-name { position: absolute; top: 34px; width: 100%; text-align: center; font-family: "PT Serif", serif; font-size: 12px; color: #111; }
  .day-date { position: absolute; top: 53px; width: 100%; text-align: center; font-size: 9px; color: #333; }
  .day .gauge { position: absolute; left: 50%; top: 79px; width: 104px; height: 104px; margin-left: -52px; }
  .day .level-pill { position: absolute; left: 50%; top: 175px; margin-left: -45px; width: 90px; height: 20px; font-size: 8.5px; }
  .forecast-rule { position: absolute; left: 32px; top: 219px; width: 878px; height: 1px; background: var(--rule); }

  .level-pill {
    display: flex; align-items: center; justify-content: center; border-radius: 999px;
    font-family: "Montserrat", sans-serif; font-weight: 700; color: #fff; letter-spacing: .3px;
    box-shadow: inset 0 -2px 0 rgba(0,0,0,.12);
  }
  .is-slight { background: linear-gradient(180deg, var(--slight-light), var(--slight)); }
  .is-average { background: linear-gradient(180deg, var(--average-light), var(--average)); }
  .is-intense { background: linear-gradient(180deg, var(--intense-light), var(--intense)); }
  .is-extreme { background: linear-gradient(180deg, var(--extreme-light), var(--extreme)); }

  .legend { position: absolute; left: 0; width: 100%; top: 232px; display: flex; justify-content: center; align-items: center; gap: 8px; padding-left: 12px; }
  .legend-swatch { width: 40px; height: 12px; border-radius: 999px; }
  .legend-label { font-family: "Montserrat", sans-serif; font-weight: 700; font-size: 9px; color: #222; margin-right: 4px; }

  .sample-gauge { position: absolute; left: 130px; top: 806px; width: 163px; height: 163px; }
  .sample-pill { position: absolute; left: 143px; top: 952px; width: 136px; height: 31px; font-size: 14px; }
  .key { position: absolute; left: 366px; top: 856px; color: var(--text); }
  .key-colours { font-size: 20.5px; white-space: nowrap; }
  .key-colours .sep { color: #333; margin: 0 8px; }
  .c-slight { color: #22a24a; } .c-average { color: #f5b400; } .c-intense { color: #ef6a1f; } .c-extreme { color: #b8141d; }
  .key-note { font-size: 19px; line-height: 29px; margin-top: 2px; }
  .key-note + .key-note { margin-top: 0; }
</style>
</head>
<body>

<svg width="0" height="0" style="position:absolute" aria-hidden="true">
  <defs>
    <radialGradient id="badge-shine" cx="40%" cy="35%" r="70%">
      <stop offset="0" stop-color="#fff" stop-opacity=".28"/>
      <stop offset="1" stop-color="#fff" stop-opacity="0"/>
    </radialGradient>
    <g id="gauge-dial">
      <path d="M -75.4 52.8 A 92 92 0 1 1 75.4 52.8 L 45.9 32.1 A 56 56 0 1 0 -45.9 32.1 Z" fill="#fff" stroke="#222" stroke-width="1.8" stroke-linejoin="round"/>
      <g fill="none" stroke-width="20">
        <circle r="76" stroke="#0f9d4f" stroke-dasharray="44.5 600" transform="rotate(146)"/>
        <circle r="76" stroke="#39b54a" stroke-dasharray="44.5 600" transform="rotate(181.5)"/>
        <circle r="76" stroke="#fbc316" stroke-dasharray="44.5 600" transform="rotate(217)"/>
        <circle r="76" stroke="#f7a21b" stroke-dasharray="44.5 600" transform="rotate(252.5)"/>
        <circle r="76" stroke="#ea6b26" stroke-dasharray="44.5 600" transform="rotate(288)"/>
        <circle r="76" stroke="#e2402a" stroke-dasharray="44.5 600" transform="rotate(323.5)"/>
        <circle r="76" stroke="#d71f2b" stroke-dasharray="44.5 600" transform="rotate(359)"/>
      </g>
      <circle r="56" fill="#fff" stroke="#222" stroke-width="1.8"/>
    </g>
  </defs>
</svg>

<section class="board-head">
  <h1 class="board-title">Mosquito Forecast</h1>
  <p class="board-subtitle">Mockup 3- size 1200X630 px | Vector Format</p>

  <div class="post">
    <div class="post-photo" role="img" aria-label="Blurred photo of a house behind tall green grass"></div>
    <h2 class="post-title">MOSCUITO FORECAST</h2>
    <p class="post-area">Greater Milwakukee</p>

    <div class="forecast-panel">
      <div class="forecast-days">
        <div class="day">
          <p class="day-name">Mon Day</p><p class="day-date">02/20</p>
          <svg class="gauge" viewBox="-100 -100 200 200"><use href="#gauge-dial"/><circle r="46" fill="var(--slight)" role="img" aria-label="Mosquito icon on green badge"/><circle r="46" fill="url(#badge-shine)"/></svg>
          <div class="level-pill is-slight">SLIGHT</div>
        </div>
        <div class="day">
          <p class="day-name">Tues Day</p><p class="day-date">02/21</p>
          <svg class="gauge" viewBox="-100 -100 200 200"><use href="#gauge-dial"/><circle r="46" fill="var(--average)" role="img" aria-label="Mosquito icon on yellow badge"/><circle r="46" fill="url(#badge-shine)"/></svg>
          <div class="level-pill is-average">AVERAGE</div>
        </div>
        <div class="day">
          <p class="day-name">Wednes Day</p><p class="day-date">02/22</p>
          <svg class="gauge" viewBox="-100 -100 200 200"><use href="#gauge-dial"/><circle r="46" fill="var(--intense)" role="img" aria-label="Mosquito icon on orange badge"/><circle r="46" fill="url(#badge-shine)"/></svg>
          <div class="level-pill is-intense">INTENSE</div>
        </div>
        <div class="day">
          <p class="day-name">Thurs Day</p><p class="day-date">02/23</p>
          <svg class="gauge" viewBox="-100 -100 200 200"><use href="#gauge-dial"/><circle r="46" fill="var(--extreme)" role="img" aria-label="Mosquito icon on red badge"/><circle r="46" fill="url(#badge-shine)"/></svg>
          <div class="level-pill is-extreme">EXTREME</div>
        </div>
        <div class="day">
          <p class="day-name">Fri Day</p><p class="day-date">02/24</p>
          <svg class="gauge" viewBox="-100 -100 200 200"><use href="#gauge-dial"/><circle r="46" fill="var(--average)" role="img" aria-label="Mosquito icon on yellow badge"/><circle r="46" fill="url(#badge-shine)"/></svg>
          <div class="level-pill is-average">AVERAGE</div>
        </div>
        <div class="day">
          <p class="day-name">Satur Day</p><p class="day-date">02/25</p>
          <svg class="gauge" viewBox="-100 -100 200 200"><use href="#gauge-dial"/><circle r="46" fill="var(--intense)" role="img" aria-label="Mosquito icon on orange badge"/><circle r="46" fill="url(#badge-shine)"/></svg>
          <div class="level-pill is-intense">INTENSE</div>
        </div>
        <div class="day">
          <p class="day-name">Sun Day</p><p class="day-date">02/26</p>
          <svg class="gauge" viewBox="-100 -100 200 200"><use href="#gauge-dial"/><circle r="46" fill="var(--slight)" role="img" aria-label="Mosquito icon on green badge"/><circle r="46" fill="url(#badge-shine)"/></svg>
          <div class="level-pill is-slight">SLIGHT</div>
        </div>
      </div>
      <div class="forecast-rule"></div>
      <div class="legend">
        <span class="legend-swatch is-slight"></span><span class="legend-label">SLIGHT</span>
        <span class="legend-swatch is-average"></span><span class="legend-label">AVERAGE</span>
        <span class="legend-swatch is-intense"></span><span class="legend-label">INTENSE</span>
        <span class="legend-swatch is-extreme"></span><span class="legend-label">EXTREME</span>
      </div>
    </div>
  </div>
</section>

<svg class="sample-gauge" viewBox="-100 -100 200 200"><use href="#gauge-dial"/><circle r="46" fill="var(--slight)" role="img" aria-label="Mosquito icon on green badge"/><circle r="46" fill="url(#badge-shine)"/></svg>
<div class="level-pill is-slight sample-pill">SLIGHT</div>

<div class="key">
  <p class="key-colours"><span class="c-slight">Slight: Green</span><span class="sep">|</span><span class="c-average">Average: Yellow</span><span class="sep">|</span><span class="c-intense">Intense : Orange</span><span class="sep">|</span><span class="c-extreme">Intense: RED</span></p>
  <p class="key-note">Slide stopper is used in this slider</p>
  <p class="key-note">Mosquite color also changed as per the forecast</p>
</div>

</body>
</html>
```